Redesign of business card for Cedar Ridge Mechanical

We are looking for a new design for our business cards for Cedar Ridge Mechanical. We are a plumbing & HVAC construction company, operating on the West Coast of Canada and USA. Logo attached.
Industry/Entity Type
Construction - Plumbing & HVAC
Contact Information for Business Card
Name, address, phone numbers, email, website address
Look and feel
Each slider illustrates characteristics of the customer's brand and the style your logo design should communicate.

```html
<!DOCTYPE html>
<html lang="en">
<head>
<meta charset="UTF-8">
<title>Cedar Ridge Mechanical – Business Card</title>
<link href="https://fonts.googleapis.com/css2?family=Poppins:wght@300;400;600&display=swap" rel="stylesheet">
<style>
  :root {
    --stage: #1d1d1e;
    --card: #222224;
    --ink: #ffffff;
    --ink-soft: #e6e6e6;
  }
  * { margin: 0; padding: 0; box-sizing: border-box; }
  html, body {
    width: 1200px; height: 711px; overflow: hidden;
    background: var(--stage);
    font-family: "Poppins", sans-serif;
    color: var(--ink);
  }
  .stage {
    width: 1200px; height: 711px;
    display: flex; align-items: center; justify-content: center; gap: 50px;
  }
  .card {
    position: relative;
    width: 520px; height: 297px;
    background: var(--card);
    border-radius: 3px;
  }
  .card-front {
    display: flex; align-items: center; justify-content: center;
  }
  .brand {
    display: flex; align-items: center; gap: 12px;
    font-weight: 600; letter-spacing: 0.04em; text-transform: uppercase;
  }
  .brand-square {
    width: 14px; height: 14px; background: var(--ink);
  }
  .card-front .brand { font-size: 24px; }
  .card-back .brand {
    position: absolute; top: 46px; right: 36px; font-size: 15px;
  }
  .card-back .brand-square { width: 10px; height: 10px; }
  .rule {
    position: absolute; left: 205px; right: 28px; top: 128px;
    height: 1.5px; background: var(--ink);
  }
  .person {
    position: absolute; left: 34px; top: 92px;
  }
  .person-name { font-size: 25px; line-height: 1.2; white-space: nowrap; }
  .person-first { font-weight: 600; }
  .person-last { font-weight: 300; }
  .person-title { font-size: 13px; font-weight: 400; margin-top: 8px; color: var(--ink-soft); }
  .contact {
    position: absolute; right: 36px; top: 146px;
    text-align: right; font-size: 12.5px; font-weight: 300; line-height: 1.45;
    color: var(--ink-soft);
  }
  .contact-address { margin-bottom: 8px; }
  .contact-line { display: flex; justify-content: flex-end; align-items: center; gap: 8px; }
  .contact-icon { width: 11px; height: 11px; fill: var(--ink); }
  .icon-spacer { width: 11px; }
</style>
</head>
<body>
<main class="stage">
  <section class="card card-front" aria-label="Card front">
    <div class="brand"><span class="brand-square"></span>Cedar Ridge Mechanical</div>
  </section>

  <section class="card card-back" aria-label="Card back">
    <div class="brand"><span class="brand-square"></span>Cedar Ridge Mechanical</div>
    <div class="rule"></div>
    <div class="person">
      <p class="person-name"><span class="person-first">Marta</span> <span class="person-last">Kovel</span></p>
      <p class="person-title">Founder &amp; CEO</p>
    </div>
    <div class="contact">
      <div class="contact-address">
        <p class="contact-line">4180 Harbor Ln. Suite 310<span class="icon-spacer"></span></p>
        <p class="contact-line">Portland, OR 97205<span class="icon-spacer"></span></p>
      </div>
      <p class="contact-line">(503) 555-0148
        <svg class="contact-icon" viewBox="0 0 24 24" aria-hidden="true"><path d="M6.6 10.8a15 15 0 0 0 6.6 6.6l2.2-2.2c.3-.3.7-.4 1-.2 1.1.4 2.3.6 3.6.6.6 0 1 .4 1 1V20c0 .6-.4 1-1 1A17 17 0 0 1 3 4c0-.6.4-1 1-1h3.5c.6 0 1 .4 1 1 0 1.3.2 2.5.6 3.6.1.3 0 .7-.2 1z"/></svg>
      </p>
      <p class="contact-line">www.cedarridgemech.com
        <svg class="contact-icon" viewBox="0 0 24 24" aria-hidden="true"><circle cx="12" cy="12" r="10" fill="none" stroke="#fff" stroke-width="2"/><path d="M2 12h20M12 2c3 3 3 17 0 20M12 2c-3 3-3 17 0 20" fill="none" stroke="#fff" stroke-width="1.6"/></svg>
      </p>
      <p class="contact-line">info@cedarridgemech.com
        <svg class="contact-icon" viewBox="0 0 24 24" aria-hidden="true"><rect x="2" y="5" width="20" height="14" rx="1.5" fill="none" stroke="#fff" stroke-width="2"/><path d="M2 6l10 7 10-7" fill="none" stroke="#fff" stroke-width="2"/></svg>
      </p>
      <p class="contact-line">www.cedarridgemech.com<span class="icon-spacer"></span></p>
    </div>
  </section>
</main>
</body>
</html>
```